Larkmoor Drones Business Card

We are a new company based in Central Queensland, Australia that uses specalised drones (Voskel Ferra Q80) to undertake mainly agricultural operations, like spraying weeds, spraying crops, spreading seed etc. I have attached a Plimbo proof of a card I was thinking along the lines of - purely a start point. The drone used in the business card MUST be a Voskel Ferra Q80.
I am very open to other ideas, especially fonts and layout. I don't have website etc set up yet.
The images are stock and easily interchangeable, I just ask that any background images reflect the local central Queensland area. The photo of the drone is not even complete (propellers cut off) and I need a new stock photo – I’m not sure if this is an issue, or I can pay for an image if need be. PLEASE FIND AN FERRA Q80 image - 4 sprayers, not 6.
The logo/business name is very draft and looking for further ideas, ideally incorporating drones or agriculture design elements into the design of the business name. The business name needs work on the graphic/design – it is a draft that I have included, the drone propellers (being a different colour) are DRAFT only and intended for changes. PLEASE DO NOT USE THE DRONE PORPELLER I HAVE USED AS A DRAFT. TRY TO FIND SOMETHING ELSE.. The arrow is a shape and not aligned in any way, I would also like ideas on different fonts and additional elements, like air streams, aviation elements, aviation or country western (farming like) themes and fonts etc.
Ideally looking at staying within the blue, green and yellow colours, keeping with an natural, outdoorsy, environmental feel.

Target Market(s)

Farmers, Agriculture, Local Governments, Land Managers

Industry/Entity Type

Agriculture, Drones, Aviation

Contact Information for Business Card

Agricultural Drone (Voskel Ferra Q80), Farming, Business Name.

Font styles to use
Sans Serif

Colors
0054AA
0677BA
7BADD7
CADEEF
E8F1F8
0094D4
00A9DD
6FCCEA
C7EBF8
E9F6FB
00AB8E
00BBA5
67D7C9
C6EFE9
E9F9F6
59FF00
82FF00
B8FF75
E3FFCB
F4FFEA

Requirements
Must have
• Voskel Ferra Q80 Drone
Should not have
• Tractors

```html
<!DOCTYPE html>
<html lang="en">
<head>
<meta charset="utf-8">
<title>Larkmoor Drones – Business Card</title>
<link rel="stylesheet" href="https://fonts.googleapis.com/css2?family=Montserrat:ital,wght@0,600;0,700;0,800;1,800&family=Cinzel:wght@600&display=swap">
<style>
  :root {
    --slate-blue: #4b5d74;
    --olive-green: #818c3a;
    --paper: #ffffff;
    --stage: #eeeeee;
    --ink: #1f1f1f;
  }
  * { box-sizing: border-box; margin: 0; padding: 0; }
  html, body { width: 1200px; height: 1199px; overflow: hidden; }
  body {
    background: var(--stage);
    font-family: "Montserrat", Arial, sans-serif;
    position: relative;
  }
  .card {
    position: absolute;
    left: 250px;
    width: 700px;
    height: 400px;
    background: var(--paper);
    overflow: hidden;
  }
  .card--front { top: 170px; }
  .card--back { top: 630px; }

  /* Front */
  .front-band--top { position: absolute; left: 0; top: 0; width: 100%; height: 182px; background: var(--slate-blue); }
  .front-band--middle { position: absolute; left: 0; top: 182px; width: 100%; height: 183px; background: var(--olive-green); }
  .front-logo {
    position: absolute; left: 0; width: 100%; top: 132px;
    text-align: center; color: var(--paper);
  }
  .wordmark {
    font-weight: 800; letter-spacing: 1px; line-height: 1.05; text-transform: uppercase;
  }
  .front-logo .wordmark { font-size: 44px; }
  .tagline {
    font-family: "Cinzel", Georgia, serif; font-weight: 600;
    font-variant: small-caps; letter-spacing: 1px;
  }
  .front-logo .tagline { font-size: 16px; margin-top: 10px; }

  /* Back */
  .holder { position: absolute; left: 34px; top: 54px; }
  .holder-name {
    font-size: 29px; font-weight: 800; font-style: italic;
    color: var(--olive-green); letter-spacing: .5px; text-transform: uppercase; line-height: 1;
  }
  .holder-title {
    font-size: 18px; font-weight: 700; color: var(--slate-blue);
    text-transform: uppercase; margin-top: 4px;
  }
  .contact-list { position: absolute; left: 34px; top: 178px; list-style: none; }
  .contact-item {
    display: flex; align-items: flex-start; gap: 8px;
    font-size: 18px; font-weight: 600; color: var(--slate-blue);
    text-transform: uppercase; line-height: 24px; margin-bottom: 4px;
  }
  .contact-item svg { flex: 0 0 20px; width: 20px; height: 20px; margin-top: 2px; fill: var(--olive-green); }
  .contact-item--address { align-items: center; }
  .back-logo {
    position: absolute; left: 390px; width: 262px; top: 82px; text-align: center;
  }
  .back-logo .wordmark { font-size: 30px; color: var(--slate-blue); }
  .back-logo .tagline { font-size: 12px; color: var(--ink); margin-top: 8px; }
  .drone-photo {
    position: absolute; left: 400px; top: 215px; width: 252px; height: 98px;
    background: radial-gradient(ellipse at center, #b9b9b4 0%, #6f7270 45%, #f4f4f4 80%);
    border-radius: 6px;
  }
  .back-band { position: absolute; bottom: 0; height: 34px; }
  .back-band--green { left: 0; width: 349px; background: var(--olive-green); }
  .back-band--blue { left: 349px; right: 0; background: var(--slate-blue); }
</style>
</head>
<body>

<section class="card card--front" aria-label="Card front">
  <div class="front-band--top"></div>
  <div class="front-band--middle"></div>
  <div class="front-logo">
    <div class="wordmark">Larkmoor<br>Drones</div>
    <div class="tagline">Servicing Central Queensland</div>
  </div>
</section>

<section class="card card--back" aria-label="Card back">
  <div class="holder">
    <h1 class="holder-name">Jordan Hale</h1>
    <p class="holder-title">CEO &amp; Founder</p>
  </div>

  <ul class="contact-list">
    <li class="contact-item">
      <svg viewBox="0 0 24 24" aria-hidden="true"><path d="M6.6 10.8a15.1 15.1 0 0 0 6.6 6.6l2.2-2.2a1 1 0 0 1 1-.25 11.4 11.4 0 0 0 3.6.57 1 1 0 0 1 1 1V20a1 1 0 0 1-1 1A17 17 0 0 1 3 4a1 1 0 0 1 1-1h3.5a1 1 0 0 1 1 1c0 1.25.2 2.45.57 3.57a1 1 0 0 1-.25 1z"/></svg>
      <span>+61 7 4920 3318</span>
    </li>
    <li class="contact-item">
      <svg viewBox="0 0 24 24" aria-hidden="true"><path d="M12 2a10 10 0 1 0 0 20 10 10 0 0 0 0-20zm6.9 6h-2.9a15.7 15.7 0 0 0-1.4-3.6A8 8 0 0 1 18.9 8zM12 4a14 14 0 0 1 1.9 4h-3.8A14 14 0 0 1 12 4zM4.3 14a8 8 0 0 1 0-4h3.4a16.5 16.5 0 0 0 0 4zm.8 2h2.9a15.7 15.7 0 0 0 1.4 3.6A8 8 0 0 1 5.1 16zM8 8H5.1a8 8 0 0 1 4.3-3.6A15.7 15.7 0 0 0 8 8zm4 12a14 14 0 0 1-1.9-4h3.8A14 14 0 0 1 12 20zm2.3-6H9.7a14.7 14.7 0 0 1 0-4h4.6a14.7 14.7 0 0 1 0 4zm.3 5.6a15.7 15.7 0 0 0 1.4-3.6h2.9a8 8 0 0 1-4.3 3.6zM16.3 14a16.5 16.5 0 0 0 0-4h3.4a8 8 0 0 1 0 4z"/></svg>
      <span>larkmoordrones.com</span>
    </li>
    <li class="contact-item">
      <svg viewBox="0 0 24 24" aria-hidden="true"><path d="M3 5h18a1 1 0 0 1 1 1v12a1 1 0 0 1-1 1H3a1 1 0 0 1-1-1V6a1 1 0 0 1 1-1zm9 7.5L20 7H4z"/></svg>
      <span>jordan@larkmoordrones.com</span>
    </li>
    <li class="contact-item contact-item--address">
      <svg viewBox="0 0 24 24" aria-hidden="true"><path d="M12 2a7 7 0 0 0-7 7c0 5.2 7 13 7 13s7-7.8 7-13a7 7 0 0 0-7-7zm0 9.5A2.5 2.5 0 1 1 12 6.5a2.5 2.5 0 0 1 0 5z"/></svg>
      <span>18 Boundary Road,<br>Unit 4, Emerald,<br>QLD 4720</span>
    </li>
  </ul>

  <div class="back-logo">
    <div class="wordmark">Larkmoor<br>Drones</div>
    <div class="tagline">Servicing Central Queensland</div>
  </div>

  <div class="drone-photo" role="img" aria-label="Photo of a Voskel Ferra Q80 agricultural spray drone with four sprayers, front view"></div>

  <div class="back-band back-band--green"></div>
  <div class="back-band back-band--blue"></div>
</section>

</body>
</html>
```